Klassisches Visitenkarten-Design mit braunen Farbtönen gesucht
Zielgruppe
Meine Firma bietet Pferdezahnbehandlungen, Pferdefütterungsberatung sowie Trensen- und Gebissanpassungen an. Ausserdem habe ich eine mobile Pferdewaage. Meine Kunden sind Pferdebesitzer der gehobenen Klasse, die gerne Geld in die Hand nehmen um ihr Tier korrekt zu halten/versorgen.
Ich setze bisher auf ein klassisches Design in braun Tönen.
Aufgabenstellung
Mir ist eine klare, schnörkellose Botschaft wichtig.
Ich möchte mich gerne mit klassischem, aber auch sehr schönem Design von der Konkurrenz abheben.
Der Fokus soll auf der wissenschaftlichen Arbeitsweise mit dem Partner Pferd liegen.
Im Anhang sind Fotos von der alten Visitenkarten. Dort fehlt mir aber die klare Linie.
Normalerweise arbeite ich mit der Schriftart Eurostyle, bin aber auch für neue Vorschläge offen.

```html
<!DOCTYPE html>
<html lang="de">
<head>
<meta charset="utf-8">
<title>EQUIVO – Visitenkarte</title>
<link rel="stylesheet" href="https://fonts.googleapis.com/css2?family=Michroma&family=Jura:wght@400;500;600&display=swap">
<style>
  :root {
    --bg: #eceae6;
    --card: #ffffff;
    --brown-dark: #5a2710;
    --brown-mid: #8a4526;
    --copper: #b9714b;
    --copper-light: #d39a78;
    --font-head: "Michroma", "Arial", sans-serif;
    --font-body: "Jura", "Arial", sans-serif;
  }
  * { box-sizing: border-box; margin: 0; padding: 0; }
  html, body {
    width: 1200px; height: 873px; overflow: hidden;
    background: var(--bg);
  }
  .sheet {
    position: relative; width: 1200px; height: 873px;
    display: flex; justify-content: center; align-items: center; gap: 70px;
  }
  .card {
    position: relative; width: 400px; height: 620px;
    background: var(--card);
    box-shadow: 0 2px 10px rgba(0,0,0,0.08);
  }

  /* Vorderseite */
  .front-frame {
    position: absolute; left: 28px; top: 0;
    width: 334px; height: 438px;
    border-left: 1.5px solid var(--brown-mid);
    border-bottom: 1.5px solid var(--brown-mid);
  }
  .wordmark {
    position: absolute; right: 38px; top: 370px;
    display: flex; align-items: flex-end; gap: 6px;
    font-family: var(--font-head); font-size: 46px; line-height: 1;
    color: var(--brown-dark); letter-spacing: 1px;
  }
  .wordmark-dot {
    width: 10px; height: 10px; border-radius: 50%;
    background: var(--brown-dark); margin-bottom: 4px;
  }
  .services {
    position: absolute; right: 38px; top: 448px;
    text-align: right; font-family: var(--font-body); text-transform: uppercase;
    line-height: 1.25;
  }
  .services .s1 { color: var(--brown-dark); font-size: 19px; font-weight: 500; letter-spacing: 0.5px; }
  .services .s2 { color: var(--copper); font-size: 16px; font-weight: 500; letter-spacing: 0.6px; }
  .services .s3 { color: var(--copper-light); font-size: 24px; font-weight: 400; letter-spacing: 0.8px; }

  /* Rückseite */
  .back { text-align: center; }
  .back-brand {
    position: absolute; top: 120px; left: 0; right: 0;
    font-family: var(--font-head); font-size: 30px; color: var(--brown-dark);
    letter-spacing: 1px;
  }
  .person { position: absolute; top: 232px; left: 0; right: 0; }
  .person-name {
    font-family: var(--font-head); font-size: 21px; color: var(--brown-dark);
    letter-spacing: 0.5px;
  }
  .person-title {
    margin-top: 8px;
    font-family: var(--font-body); font-size: 13px; color: var(--brown-mid);
  }
  .address {
    position: absolute; top: 318px; left: 0; right: 0;
    font-family: var(--font-body); font-style: normal;
    font-size: 19px; line-height: 1.4; color: var(--brown-mid);
  }
  .contact {
    position: absolute; top: 412px; left: 0; right: 0;
    font-family: var(--font-body); font-size: 19px; line-height: 1.4;
    color: var(--copper);
  }
</style>
</head>
<body>
<main class="sheet">
  <section class="card front" aria-label="Vorderseite">
    <div class="front-frame"></div>
    <div class="wordmark">EQUIVO<span class="wordmark-dot"></span></div>
    <div class="services">
      <p class="s1">Pferdezahnbehandlung</p>
      <p class="s2">Pferdefütterungsberatung</p>
      <p class="s3">Mobile Pferdewaage</p>
    </div>
  </section>

  <section class="card back" aria-label="Rückseite">
    <div class="back-brand">EQUIVO</div>
    <div class="person">
      <p class="person-name">MARLENE T. VOGT</p>
      <p class="person-title">Agrarwissenschaften (Dr. sc.)</p>
    </div>
    <address class="address">
      Lindenweg 14<br>
      79865 Talbach/Südschwarzwald
    </address>
    <div class="contact">
      <p>0170 5583921</p>
      <p>kontakt@equi-dental.com</p>
      <p>www.equivo.de</p>
    </div>
  </section>
</main>
</body>
</html>
```